Herbalist's Pain Cream WIX Website Redesign

I need a complete WIX website redesign! I am an herbalist and I'm relaunching my company, starting with a pain cream as the flagship product. My natural pain relief cream is composed of 6 active botanicals, uses all natural preservatives and provides pain relief within 1 minute! I have a new label design that reflects the high quality of this product and its ingredients. I have the content written and a rough website outline. I want the new website to match the color scheme of the label, and to show the quality of the product. (Logo uploaded is older color scheme. See New Label upload for updated color scheme.) I will be launching more products in the future, but the current content is for 1 flagship product. I want a high quality, earthy/ natural, botanical medicine feel. SEO phrase "Natural Pain Relief Cream" Old website is up again, for pictures: www.fennowroots.com

Target Market(s)

Middle to later aged women, Same for Men, but usually introduced by woman in their life

Industry/Entity Type

Botanical Supplement

Coding

Coded - Design and coding required

Number of Pages Required

5+ page

Colors
0054AA
0677BA
7BADD7
CADEEF
E8F1F8

Requirements
Must have
• Homepage, About, Ingredients, Shop, Contact Us
Nice to have
• FAQ section, maybe graphics to highlight unique elements

```html
<!DOCTYPE html>
<html lang="en">
<head>
<meta charset="utf-8">
<title>Wrenfield Herbal Remedies – Home and Contact Pages</title>
<link href="https://fonts.googleapis.com/css2?family=Outfit:wght@400;500;600;700;800&family=Playfair+Display:wght@600&display=swap" rel="stylesheet">
<style>
:root{
  --blue:#0054AA;
  --blue-mid:#0677BA;
  --blue-soft:#7BADD7;
  --blue-pale:#CADEEF;
  --blue-mist:#E8F1F8;
  --ink:#151515;
  --black:#111111;
  --grey-text:#3a3a3a;
  --field:#eef1f4;
  --board:#dbe5ef;
}
*{margin:0;padding:0;box-sizing:border-box}
html,body{width:787px;height:1200px;overflow:hidden}
body{background:var(--board);font-family:"Outfit",sans-serif;color:var(--ink);position:relative}

.board-title{position:absolute;top:26px;font-weight:700;font-size:21px;color:var(--blue);width:300px;text-align:center;letter-spacing:-.2px}
.board-title.home-title{left:88px}
.board-title.contact-title{left:411px}

.page{position:absolute;width:294px;background:#fff;overflow:hidden}
.page.home{left:78px;top:67px;height:1116px}
.page.contact{left:414px;top:69px;height:448px}
.block{position:absolute;left:0;width:294px}

.topbar{top:0;height:7.5px;background:var(--black);color:#fff;font-size:2.5px;display:flex;align-items:center;justify-content:space-between;padding:0 32px}
.topbar .follow{display:flex;align-items:center;gap:1.5px}
.topbar .dot{width:2.4px;height:2.4px;border-radius:50%;background:#fff;display:inline-block}

.nav{top:7.5px;height:20px;background:var(--blue)}
.brand{position:absolute;display:flex;align-items:center;gap:2.5px;color:#fff;font-weight:500;font-size:6px;letter-spacing:.2px;white-space:nowrap}
.nav .brand{left:32px;top:6px}
.brand .mark{width:8px;height:8px;border-radius:50%;background:#fff;display:inline-block}
.menu{position:absolute;left:111px;top:0;height:20px;display:flex;align-items:center;gap:7.5px;color:#fff;font-size:3.4px}
.menu .shop{background:var(--black);border-radius:5px;padding:2.2px 5px;margin-left:1px}
.nav-icons{position:absolute;right:31px;top:6px;display:flex;gap:4px}

.btn{position:absolute;display:flex;align-items:center;justify-content:center;border-radius:5px;font-size:3.3px;color:#fff;background:var(--blue)}
.btn.dark{background:var(--black)}
.btn.outline{background:transparent;border:.6px solid #fff}

.hero{top:28px;height:92px;background:linear-gradient(100deg,#3a4a40 0%,#25302a 35%,#0c0e0d 65%,#121816 100%)}
.hero-copy{position:absolute;left:173px;top:17px;color:#fff}
.hero-copy .kicker{font-size:3.3px;letter-spacing:.3px}
.hero-copy h1{font-size:10.4px;font-weight:600;line-height:12.2px;margin-top:2.5px}
.hero-copy p{font-size:3.3px;margin-top:3px}
.hero-dots{position:absolute;left:140px;top:84px;display:flex;gap:3px}
.hero-dots span{width:1.6px;height:1.6px;border-radius:50%;background:#bbb}
.hero-dots span:first-child{background:#fff}

.features{top:120px;height:84px}
.feature{position:absolute;top:12px;width:72px;text-align:center}
.feature .icon{width:22px;height:22px;margin:0 auto;display:block}
.feature h3{font-size:4px;font-weight:600;margin-top:7px}
.feature p{font-size:3.2px;line-height:5.8px;margin-top:2.5px;color:var(--grey-text)}

.relief{top:204px;height:104px;background:linear-gradient(90deg,#f1f3f5,#fbfbfb)}
.relief .photo{position:absolute;left:142px;top:0;width:152px;height:104px;background:linear-gradient(120deg,#e8e4de 0%,#d9d3cb 45%,#c8c2bb 100%)}
.tag{position:absolute;background:#fff;color:var(--blue);font-size:3px;border-radius:4px;padding:1.2px 4px;white-space:nowrap}
.relief .tag{left:32px;top:19px}
.relief h2{position:absolute;left:32px;top:29px;font-size:6.5px;font-weight:600;line-height:9px}
.relief h2 span{color:var(--blue)}
.relief p{position:absolute;left:32px;top:51px;width:104px;font-size:3.2px;line-height:5.6px;color:var(--grey-text)}

.herbs{top:308px;height:230px;text-align:center}
.herbs h2{position:absolute;left:40px;top:18px;width:214px;font-size:6.6px;font-weight:600;line-height:9.3px;color:var(--blue)}
.herbs .intro{position:absolute;left:44px;top:41px;width:206px;font-size:3.2px;line-height:5.6px;color:var(--grey-text)}
.herb{position:absolute;display:flex;align-items:flex-end;justify-content:flex-end;padding:0 2.5px 2px 0;color:#fff;font-weight:700;font-size:5px}
.herb.arnica{left:36px;top:77px;width:94px;height:48px;background:linear-gradient(160deg,#4a6a22,#2d4514)}
.herb.birch{left:132px;top:77px;width:62px;height:48px;background:linear-gradient(160deg,#c98a18,#7a4a10)}
.herb.yarrow{left:197px;top:77px;width:62px;height:48px;background:linear-gradient(160deg,#6a7f58,#3b4f34)}
.herb.copaiba{left:36px;top:127px;width:62px;height:49px;background:linear-gradient(160deg,#5a4a2c,#3a3320)}
.herb.sage{left:100px;top:127px;width:62px;height:49px;background:linear-gradient(160deg,#8c7aa6,#4f5a38)}
.herb.ylang{left:165px;top:127px;width:94px;height:49px;background:linear-gradient(160deg,#2e5a24,#c9b12a 60%,#2c4a1c)}
.herbs .tagline{position:absolute;left:52px;top:184px;width:190px;font-family:"Playfair Display",serif;font-weight:600;font-size:6.2px;line-height:8.6px;color:var(--ink)}

.founder{top:538px;height:118px;background:linear-gradient(120deg,#1f5bb0,#1a4f9c)}
.founder .strip{position:absolute;left:0;top:0;width:30px;height:118px;background:#174a94}
.founder .portrait{position:absolute;left:32px;top:-3px;width:93px;height:124px;border:1.5px solid #fff;border-radius:3px;background:linear-gradient(180deg,#8a96a3 0%,#b0a79b 45%,#6d6458 100%)}
.founder .tag{left:141px;top:15px;color:var(--blue)}
.founder h2{position:absolute;left:141px;top:22px;font-size:6.5px;font-weight:500;line-height:9px;color:#fff}
.founder p{position:absolute;left:141px;top:44px;width:124px;font-size:3.2px;line-height:5.8px;color:#fff}

.testimonials{top:656px;height:134px;text-align:center}
.testimonials .tag{left:117px;top:14px;background:var(--blue-mist)}
.testimonials h2{position:absolute;left:0;width:294px;top:21px;font-size:7px;font-weight:600}
.quote-card{position:absolute;top:39px;height:80px;background:#f2f4f6;border-radius:3px;text-align:left;padding:9px 12px}
.quote-card.main{left:47px;width:201px}
.quote-card.side-left{left:-170px;width:200px;opacity:.45}
.quote-card.side-right{left:270px;width:200px;opacity:.45}
.quote-card h4{font-size:4px;font-weight:500}
.quote-card p{font-size:3.2px;line-height:5.8px;color:var(--grey-text);margin-top:2.5px}
.quote-card .name{font-size:3.2px;color:var(--blue);margin-top:3.5px;font-weight:500}
.quote-card .qmark{position:absolute;right:8px;top:5px;font-size:13px;font-weight:800;color:var(--blue);line-height:1}
.arrow{position:absolute;top:75px;width:6px;height:8px}
.arrow.prev{left:37px}
.arrow.next{left:251px}

.faq{top:790px;height:169px;background:linear-gradient(180deg,#eceff2,#f4f6f8)}
.faq h2{position:absolute;left:0;width:294px;top:6px;text-align:center;font-size:8.2px;font-weight:600}
.faq-item{position:absolute;left:39px;width:218px;background:#fff;border-radius:2px;padding:0 6px}
.faq-item .q{display:flex;justify-content:space-between;align-items:center;height:13.5px;font-size:4.6px;font-weight:500;color:var(--blue)}
.faq-item .q b{font-size:6px;font-weight:600}
.faq-item .a{font-size:3.2px;line-height:5.8px;color:var(--grey-text);padding-bottom:4px}
.faq-item.open{top:30px}

.cta{height:63px;background:linear-gradient(100deg,#0b3f8f,#0a4da8 50%,#0b3f8f);text-align:center;color:#fff}
.cta h2{position:absolute;left:0;width:294px;top:11px;font-size:8.2px;font-weight:600}
.cta p{position:absolute;left:0;width:294px;top:25px;font-size:4.8px}
.cta .btn.buy{left:118px;top:41px;width:31px;height:8px;background:var(--black)}
.cta .btn.outline{left:152px;top:41px;width:31px;height:8px}

.footer{height:94px;background:var(--black);color:#fff;text-align:center}
.footer .brand{left:0;width:294px;justify-content:center;top:15px;font-size:7px}
.footer .brand .mark{width:10px;height:10px}
.footer .about{position:absolute;left:0;width:294px;top:36px;font-size:3.4px;line-height:6.2px}
.footer .rule{position:absolute;left:30px;width:234px;height:.4px;background:#3a3a3a}
.footer .links{position:absolute;left:0;width:294px;top:61px;font-size:3.2px;font-weight:500;color:var(--blue-soft);display:flex;justify-content:center;gap:3px}
.footer .links span.sep{color:#777}
.footer .copy{position:absolute;left:0;width:294px;top:85px;font-size:3.2px;color:#ccc}

.contact-hero{top:27px;height:76px;background:linear-gradient(100deg,#6fb6c3 0%,#7cc0cb 60%,#5fa7b6 100%)}
.contact-hero h1{position:absolute;left:32px;top:32px;font-size:9.5px;font-weight:600;color:#fff}
.form-area{top:103px;height:187px}
.form-area .lead{position:absolute;left:32px;top:18px;font-size:8.5px;font-weight:500}
.form-area h2{position:absolute;left:32px;top:29px;font-size:10.5px;font-weight:600;color:var(--blue)}
.form-area .intro{position:absolute;left:32px;top:45px;width:226px;font-size:3.6px;line-height:6.8px;color:var(--grey-text)}
.field{position:absolute;background:var(--field);border-radius:1.5px;font-size:3.5px;color:#7a7a7a;padding:4.5px 4.5px}
.field.msg{font-style:italic}
.form-area .btn{left:32px;top:158px;width:31px;height:7.5px}
</style>
</head>
<body>

<h2 class="board-title home-title">Home Page</h2>
<h2 class="board-title contact-title">Contact Page</h2>

<main class="page home">
  <div class="block topbar"><span>Welcome to Wrenfield Herbal Remedies!</span><span class="follow">Email: milo@wrenfieldherbs.com &nbsp;| &nbsp;Follow: <i class="dot"></i><i class="dot"></i><i class="dot"></i><i class="dot"></i></span></div>
  <nav class="block nav">
    <div class="brand"><i class="mark"></i>WRENFIELD</div>
    <div class="menu"><span>Home</span><span>About Us</span><span>Ingredients</span><span>Contact</span><span class="shop">Shop Online</span></div>
    <div class="nav-icons">
      <svg width="6" height="6" viewBox="0 0 10 10" fill="none" stroke="#fff" stroke-width="1.2"><circle cx="4.2" cy="4.2" r="3.2"/><path d="M6.6 6.6 9.3 9.3"/></svg>
      <svg width="6" height="6" viewBox="0 0 10 10" fill="none" stroke="#fff" stroke-width="1.2"><circle cx="5" cy="3.3" r="2.3"/><path d="M1 9.5c.6-2.5 2.2-3.6 4-3.6s3.4 1.1 4 3.6"/></svg>
      <svg width="6" height="6" viewBox="0 0 10 10" fill="none" stroke="#fff" stroke-width="1.2"><path d="M.5 1h1.6l1.3 5.5h5l1-4H2.6"/><circle cx="4" cy="8.6" r=".7"/><circle cx="7.8" cy="8.6" r=".7"/></svg>
    </div>
  </nav>

  <section class="block hero" role="img" aria-label="Photo of a jar of pain cream resting on a mossy rock against a dark background">
    <div class="hero-copy">
      <div class="kicker">APPLY, RELAX &amp; RECLAIM</div>
      <h1>Welcome to Wrenfield<br>Herbal Remedies</h1>
      <p>where the wisdom of nature meets the art of healing.</p>
    </div>
    <span class="btn" style="left:173px;top:62px;width:29px;height:6.5px">Shop Now</span>
    <div class="hero-dots"><span></span><span></span><span></span></div>
  </section>

  <section class="block features">
    <div class="feature" style="left:38px">
      <svg class="icon" viewBox="0 0 22 22" fill="none" stroke="var(--blue)" stroke-width=".9"><circle cx="8" cy="7" r="6" fill="var(--blue-pale)" stroke="none"/><path d="M9 4h5M10 4v6l-5 8h13l-5-8V4"/><circle cx="14.5" cy="17" r="2.2"/><circle cx="18" cy="17" r="2.2"/></svg>
      <h3>Expertly Crafted Formula</h3>
      <p>Formulated by an<br>herbalist with over a decade<br>of clinical experience.</p>
    </div>
    <div class="feature" style="left:111px">
      <svg class="icon" viewBox="0 0 22 22" fill="none" stroke="var(--blue)" stroke-width=".9"><circle cx="8" cy="7" r="6" fill="var(--blue-pale)" stroke="none"/><path d="M3 12h16c0 4-3.5 6.5-8 6.5S3 16 3 12zM8 18.5 7 20.5h8l-1-2M12 11l6-8"/><path d="M13 6l2 1"/></svg>
      <h3>Fast-Acting Ingredients</h3>
      <p>With nature's power at the<br>forefront, our 6 active botanicals<br>deliver almost instant relief.</p>
    </div>
    <div class="feature" style="left:183px">
      <svg class="icon" viewBox="0 0 22 22" fill="none" stroke="var(--blue)" stroke-width=".9"><circle cx="8" cy="7" r="6" fill="var(--blue-pale)" stroke="none"/><rect x="3" y="10" width="14" height="9" rx="2"/><path d="M3 13h14"/><ellipse cx="15.5" cy="9" rx="4" ry="3"/></svg>
      <h3>Nurturing Touch</h3>
      <p>Not only does our natural pain<br>relief cream alleviate discomfort, but<br>also it nourishes &amp; rejuvenates skin.</p>
    </div>
  </section>

  <section class="block relief">
    <div class="photo" role="img" aria-label="Photo of a woman sitting on a living room floor holding her knee"></div>
    <span class="tag">Feel the Difference in Just 1 Minute!</span>
    <h2>Apply, Relax, and Reclaim Your Day—<br><span>Experience Relief Today</span></h2>
    <p>Whether you're overcoming the strains of daily life or the demands of an active lifestyle, our natural pain relief cream is your go-to solution for quick relief.</p>
    <span class="btn" style="left:32px;top:75px;width:31px;height:7.5px">Buy Now</span>
  </section>

  <section class="block herbs">
    <h2>We use herbs harvested from the wild and from the farm, to deliver a potent natural healing experience.</h2>
    <p class="intro">At Wrenfield Herbal Remedies, we understand that when discomfort strikes, you seek swift and effective relief. That's why it is important to use the most powerful botanical ingredients in our natural pain relief cream. Each ingredient reflects a commitment to quality and efficacy, harnessing the powerful properties of nature's finest ingredients. From the strongest Yarrow cultivar on earth, grown on a 500 year old farm in Bulgaria, to a wild Arnica species harvested for us in the Cascade Mountains, we use our most powerful plant allies to ensure you get the relief you need!</p>
    <div class="herb arnica" role="img" aria-label="Photo of a yellow arnica flower">Arnica</div>
    <div class="herb birch" role="img" aria-label="Photo of golden birch leaves">Sweet Birch</div>
    <div class="herb yarrow" role="img" aria-label="Photo of white yarrow flowers">Yarrow</div>
    <div class="herb copaiba" role="img" aria-label="Photo of copaiba seed pods">Copaiba Balsam</div>
    <div class="herb sage" role="img" aria-label="Photo of clary sage blossoms">Clary Sage</div>
    <div class="herb ylang" role="img" aria-label="Photo of yellow ylang ylang flowers">Ylang Ylang</div>
    <p class="tagline">Try our natural pain relief cream and let the calming embrace<br>of nature guide you toward a place of comfort and vitality.</p>
    <span class="btn" style="left:120px;top:208px;width:50px;height:7.5px">Explore the Ingredients</span>
  </section>

  <section class="block founder">
    <div class="strip"></div>
    <div class="portrait" role="img" aria-label="Portrait of the founder outdoors in the mountains"></div>
    <span class="tag">Our Founder &amp; Research Specialist</span>
    <h2>Experience the Difference That<br>Expertise Makes!</h2>
    <p>Meet Milo, the creator of Wrenfield Herbal Remedies. Inspired by his personal journey to heal his chronic pain, he devoted his life to studying medicinal plants and how to harness their healing abilities to improve the lives of others. As a trained herbalist, botanical medicine researcher and supplement formulator, let Milo's expertise guide you back to health and wellness. Discover the restorative power of herb-based solutions at Wrenfield Herbal Remedies!</p>
    <span class="btn dark" style="left:141px;top:92px;width:52px;height:7.5px">Read More About Milo</span>
  </section>

  <section class="block testimonials">
    <span class="tag">Our Valuable Client Reviews</span>
    <h2>Testimonials</h2>
    <div class="quote-card side-left"><span class="qmark">”</span><h4>This is Magical Pain Cream</h4><p>"Milo Wren is a life changer! Between my husband and I, we have racked up the itises. We've taken the pills and tried plant based creams. But I'm a total amateur. Lol. His plant healing knowledge gave us our health back! Go read his bio.</p></div>
    <div class="quote-card main">
      <span class="qmark">”</span>
      <h4>This is Magical Pain Cream</h4>
      <p>"Milo Wren is a life changer! Believe me when I say it, this pain cream is pure magic! Between my husband and I, we have racked up the itises through car wrecks, bad luck, and growing older. We've taken the pills and tried the supplement. I've guinea pigged us both trying to make my own plant based pain reliever oils and creams because nothing was working that wasn't causing other problems. But I'm a total amateur....so...eh...Milo is a masterful REAL clinical herbalist—not the mail order kind. Lol. His plant healing knowledge is unending, and he's changed the lives of so many by giving us our health back! You won't find any other cream better than this expertly crafted jar of heavenly RELIEF! Go read his bio, and the list of ingredients. Be mind blown! THANK YOU!"</p>
      <div class="name">Nora P. Dayton, OH</div>
    </div>
    <div class="quote-card side-right"><h4>This is Magical Pain Cream</h4><p>"Milo Wren is a life changer! Believe me, my husband and I have taken the pills and creams. I'm a total amateur. His plant healing knowledge is unending. You won't find better, and the list of ingredients.</p><div class="name">Nora P. Dayton, OH</div></div>
    <svg class="arrow prev" viewBox="0 0 6 8" fill="none" stroke="#111" stroke-width="1"><path d="M4.5 .8 1.5 4l3 3.2"/></svg>
    <svg class="arrow next" viewBox="0 0 6 8" fill="none" stroke="#111" stroke-width="1"><path d="M1.5 .8 4.5 4l-3 3.2"/></svg>
  </section>

  <section class="block faq">
    <h2>Frequently Asked Questions</h2>
    <div class="faq-item open"><div class="q">1. Does it work?<b>−</b></div><p class="a">Absolutely! You will start to feel relief within 1 minute. After 15 minutes you will feel its full effects. At Wrenfield Herbal Remedies, we stand by the effectiveness of our Pain Cream, which is truly more than just a product—it's a carefully crafted solution born from clinical experience and expertise.</p></div>
    <div class="faq-item" style="top:70px"><div class="q">2. Who is this natural pain relief cream for?<b>+</b></div></div>
    <div class="faq-item" style="top:87px"><div class="q">3. How do I use it?<b>+</b></div></div>
    <div class="faq-item" style="top:104px"><div class="q">4. How long is your pain cream good for?<b>+</b></div></div>
    <div class="faq-item" style="top:121px"><div class="q">5. Are your preservatives natural?<b>+</b></div></div>
    <div class="faq-item" style="top:138px"><div class="q">6. What's your shipping and delivery times?<b>+</b></div></div>
  </section>

  <section class="block cta" style="top:959px">
    <h2>Have more questions? We're just a message away!</h2>
    <p>Embrace a life free of discomfort—order your Pain Cream today!</p>
    <span class="btn buy">Buy Now</span>
    <span class="btn outline">Contact Us</span>
  </section>

  <footer class="block footer" style="top:1022px">
    <div class="brand"><i class="mark"></i>WRENFIELD</div>
    <p class="about">At Wrenfield Herbal Remedies, we invite you to join Milo on this journey of healing<br>and discover the natural path to wellness.</p>
    <div class="rule" style="top:55px"></div>
    <div class="links"><span>HOME</span><span class="sep">|</span><span>ABOUT US</span><span class="sep">|</span><span>INGREDIENTS</span><span class="sep">|</span><span>PRODUCTS</span><span class="sep">|</span><span>SHOP NOW</span><span class="sep">|</span><span>TERMS OF USE</span></div>
    <div class="rule" style="top:73px"></div>
    <p class="copy">Wrenfield Herbal Remedies@2024. All Rights Reserved</p>
  </footer>
</main>

<main class="page contact">
  <div class="block topbar"><span>Welcome to Wrenfield Herbal Remedies!</span><span class="follow">Email: milo@wrenfieldherbs.com &nbsp;| &nbsp;Follow: <i class="dot"></i><i class="dot"></i><i class="dot"></i><i class="dot"></i></span></div>
  <nav class="block nav">
    <div class="brand"><i class="mark"></i>WRENFIELD</div>
    <div class="menu"><span>Home</span><span>About Us</span><span>Ingredients</span><span>Contact</span><span class="shop">Shop Online</span></div>
    <div class="nav-icons">
      <svg width="6" height="6" viewBox="0 0 10 10" fill="none" stroke="#fff" stroke-width="1.2"><circle cx="4.2" cy="4.2" r="3.2"/><path d="M6.6 6.6 9.3 9.3"/></svg>
      <svg width="6" height="6" viewBox="0 0 10 10" fill="none" stroke="#fff" stroke-width="1.2"><circle cx="5" cy="3.3" r="2.3"/><path d="M1 9.5c.6-2.5 2.2-3.6 4-3.6s3.4 1.1 4 3.6"/></svg>
      <svg width="6" height="6" viewBox="0 0 10 10" fill="none" stroke="#fff" stroke-width="1.2"><path d="M.5 1h1.6l1.3 5.5h5l1-4H2.6"/><circle cx="4" cy="8.6" r=".7"/><circle cx="7.8" cy="8.6" r=".7"/></svg>
    </div>
  </nav>

  <section class="block contact-hero" role="img" aria-label="Photo of a vintage telephone handset with speech bubbles on a teal background">
    <h1>Contact Us</h1>
  </section>

  <section class="block form-area">
    <p class="lead">Have more questions?</p>
    <h2>We're just a message away!</h2>
    <p class="intro">Your questions matter to us, and we take pride in offering support with a friendly touch. Your inquiries are always welcomed with open arms. Together, let's explore the natural path to wellness!</p>
    <div class="field" style="left:32px;top:66px;width:77px;height:12.6px">Enter First Name</div>
    <div class="field" style="left:114px;top:66px;width:77px;height:12.6px">Enter Last Name</div>
    <div class="field" style="left:32px;top:83px;width:77px;height:13px">Enter Email Address</div>
    <div class="field" style="left:114px;top:83px;width:77px;height:13px">Enter Phone Number</div>
    <div class="field" style="left:32px;top:102px;width:159px;height:12.6px">Subject</div>
    <div class="field msg" style="left:32px;top:119px;width:159px;height:33px">Message here...</div>
    <span class="btn dark">Submit</span>
  </section>

  <section class="block cta" style="top:290px">
    <h2>Have more questions? We're just a message away!</h2>
    <p>Embrace a life free of discomfort—order your Pain Cream today!</p>
    <span class="btn buy">Buy Now</span>
    <span class="btn outline">Contact Us</span>
  </section>

  <footer class="block footer" style="top:354px">
    <div class="brand"><i class="mark"></i>WRENFIELD</div>
    <p class="about">At Wrenfield Herbal Remedies, we invite you to join Milo on this journey of healing<br>and discover the natural path to wellness.</p>
    <div class="rule" style="top:55px"></div>
    <div class="links"><span>HOME</span><span class="sep">|</span><span>ABOUT US</span><span class="sep">|</span><span>INGREDIENTS</span><span class="sep">|</span><span>PRODUCTS</span><span class="sep">|</span><span>SHOP NOW</span><span class="sep">|</span><span>TERMS OF USE</span></div>
    <div class="rule" style="top:73px"></div>
    <p class="copy">Wrenfield Herbal Remedies@2024. All Rights Reserved</p>
  </footer>
</main>

</body>
</html>
```